Quorva - corporate Business Card

We need a good look and innovative business card for a new start up company based in Los Angeles called "Quorva". We are in a payment business, including payment card, app, and ewallet. We are expert in online payment and Card not present (CNP) transaction.
We need an innovative, modern business card.

Our logo font is Aero Matics

Target Market(s)

Startup - Bank - Online Payment - Card Manufacturing

Industry/Entity Type

Startup

Contact Information for Business Card

phone: 555 014 7396 - Address: 4172 Marlowe blvd, Ardenvale, CA 90299

Requirements
Must have
• Message: innovative, professional, expert, high tech, trust, online payment expert, security
Nice to have
• no comment
Should not have
• no Comment

```html
<!DOCTYPE html>
<html lang="en">
<head>
<meta charset="utf-8">
<title>Quorva – Business Card</title>
<link rel="stylesheet" href="https://fonts.googleapis.com/css2?family=Open+Sans:wght@400;600;700&display=swap">
<style>
  :root {
    --brand-red: #b81f2f;
    --ink: #4a4a4a;
    --paper: #ffffff;
    --stage: #ecebe8;
    --band-grey: #8a8a8a;
    --divider: #d6d6d6;
  }
  * { box-sizing: border-box; margin: 0; padding: 0; }
  html, body {
    width: 1200px; height: 987px; overflow: hidden;
    background: var(--stage);
    font-family: "Open Sans", Arial, sans-serif;
  }
  .canvas { position: relative; width: 1200px; height: 987px; }

  .card {
    position: absolute; left: 292px; width: 616px; height: 351px;
    box-shadow: 0 3px 10px rgba(0,0,0,0.18);
    overflow: hidden;
  }
  .card--front { top: 130px; background: var(--paper); }
  .card--back { top: 506px; background: var(--brand-red); }

  /* Front: brand block */
  .brand { position: absolute; left: 76px; top: 138px; display: flex; align-items: center; gap: 12px; }
  .brand__dot { width: 54px; height: 54px; border-radius: 50%; background: var(--brand-red); }
  .brand__name { font-size: 44px; font-weight: 600; color: var(--brand-red); line-height: 1; letter-spacing: 0.5px; padding-bottom: 4px; }

  .divider { position: absolute; left: 333px; top: 75px; width: 1px; height: 182px; background: var(--divider); }

  .contact { position: absolute; left: 361px; top: 81px; color: var(--ink); font-size: 16px; line-height: 1.4; }
  .contact__name { font-size: 21px; font-weight: 600; color: var(--brand-red); line-height: 1.2; letter-spacing: 0.2px; }
  .contact__role { font-size: 17px; margin-bottom: 17px; }
  .contact__address { margin-bottom: 9px; }
  .contact__line { display: flex; align-items: center; gap: 9px; }
  .contact__line svg { width: 15px; height: 15px; flex: none; }

  .footer-band { position: absolute; left: 0; bottom: 0; width: 329px; height: 11px; background: var(--band-grey); }
  .footer-tab {
    position: absolute; right: 0; bottom: 0; width: 287px; height: 41px;
    background: var(--brand-red);
    border-top-left-radius: 48px 41px;
    color: #fff; font-size: 15px; letter-spacing: 4px;
    display: flex; align-items: center; justify-content: center; padding-left: 22px;
  }

  /* Back */
  .back__disc { position: absolute; left: 213px; top: 70px; width: 188px; height: 188px; border-radius: 50%; background: var(--paper); }
  .back__url { position: absolute; left: 0; right: 0; top: 288px; text-align: center; color: #fff; font-size: 15px; letter-spacing: 4.5px; }
</style>
</head>
<body>
<main class="canvas">
  <section class="card card--front" aria-label="Business card front">
    <div class="brand">
      <span class="brand__dot"></span>
      <span class="brand__name">quorva</span>
    </div>
    <div class="divider"></div>
    <div class="contact">
      <p class="contact__name">DARA WHITFIELD</p>
      <p class="contact__role">CEO&amp;Founder</p>
      <p class="contact__address">4172 Marlowe blvd<br>Ardenvale, CA 90299</p>
      <p class="contact__line">
        <svg viewBox="0 0 16 16" aria-hidden="true"><path fill="#b81f2f" d="M3.5 1.5l2.5 3-1.5 1.8c.8 1.8 2.4 3.4 4.2 4.2l1.8-1.5 3 2.5-1.6 2.3C7.5 13.6 2.4 8.5 1.2 3.1z"/></svg>
        555 014 7396
      </p>
      <p class="contact__line">
        <svg viewBox="0 0 16 16" aria-hidden="true"><rect x="1" y="3.5" width="14" height="9" fill="#b81f2f"/><path d="M1.5 4l6.5 5 6.5-5" fill="none" stroke="#fff" stroke-width="1.2"/></svg>
        dara@quorva.com
      </p>
    </div>
    <div class="footer-band"></div>
    <div class="footer-tab">www.quorva.com</div>
  </section>

  <section class="card card--back" aria-label="Business card back">
    <div class="back__disc"></div>
    <p class="back__url">www.quorva.com</p>
  </section>
</main>
</body>
</html>
```